Business card for a new cabinet shop company named Veloran Cabinets for high end cabinets

Design a business card, thinking dark rich green with colours to speak of high end luxury ie; cream, gold, black possibly

Mitchell Tarrowby
Director Craftsman
Email: info@veloranjoinery-example.com.au
Instagram : @veloran.cabinets

```html
<!DOCTYPE html>
<html lang="en">
<head>
<meta charset="utf-8">
<title>Veloran Cabinets – Business Card</title>
<link href="https://fonts.googleapis.com/css2?family=Poppins:wght@400&family=Roboto:wght@300;400;500&display=swap" rel="stylesheet">
<style>
  :root {
    --green: #0e9444;
    --gold: #cbae67;
    --white: #ffffff;
    --ink: #1a1a1a;
    --backdrop: #f0f0f0;
  }
  html, body {
    margin: 0;
    padding: 0;
    width: 1200px;
    height: 990px;
    overflow: hidden;
    background: var(--backdrop);
  }
  .canvas {
    position: relative;
    width: 1200px;
    height: 990px;
  }
  .card {
    position: absolute;
    left: 244px;
    width: 712px;
    height: 406px;
    border-radius: 40px;
    overflow: hidden;
    box-shadow: 0 6px 18px rgba(0,0,0,0.22);
  }
  .card--front { top: 68px; background: var(--green); }
  .card--back  { top: 516px; background: var(--white); }

  .brand-circle {
    position: absolute;
    border-radius: 50%;
    box-sizing: border-box;
  }
  .wordmark {
    position: absolute;
    font-family: "Poppins", sans-serif;
    font-weight: 400;
    line-height: 1;
    margin: 0;
  }
  .wordmark__name { display: block; }
  .wordmark__sub  { display: block; text-transform: uppercase; }

  /* Front */
  .card--front .brand-circle {
    left: 165px; top: 154px; width: 100px; height: 100px;
    border: 3px solid var(--white);
  }
  .card--front .wordmark { left: 316px; top: 150px; color: var(--white); }
  .card--front .wordmark__name { font-size: 62px; letter-spacing: 0.5px; }
  .card--front .wordmark__sub  { font-size: 29px; letter-spacing: 13px; margin-top: 14px; }

  /* Back */
  .card--back .brand-circle {
    left: 36px; top: 166px; width: 76px; height: 76px;
    border: 3px solid var(--green);
  }
  .card--back .wordmark { left: 137px; top: 162px; color: var(--green); }
  .card--back .wordmark__name { font-size: 44px; }
  .card--back .wordmark__sub  { font-size: 21px; letter-spacing: 9.5px; margin-top: 10px; }

  .divider {
    position: absolute;
    left: 356px; top: 68px;
    width: 1px; height: 243px;
    background: var(--green);
  }
  .contact {
    position: absolute;
    left: 390px; top: 122px;
    font-family: "Roboto", sans-serif;
  }
  .contact__name {
    margin: 0;
    font-size: 36px;
    line-height: 1;
    white-space: nowrap;
  }
  .contact__first { color: var(--gold); font-weight: 500; }
  .contact__last  { color: var(--green); font-weight: 300; }
  .contact__role {
    margin: 6px 0 0;
    font-size: 18px;
    font-weight: 400;
    color: var(--ink);
    letter-spacing: 0.3px;
  }
  .contact__list {
    list-style: none;
    margin: 34px 0 0;
    padding: 0;
  }
  .contact__item {
    display: flex;
    align-items: center;
    gap: 11px;
    font-size: 16.5px;
    color: var(--ink);
    letter-spacing: 0.4px;
    height: 24px;
  }
  .contact__icon { width: 15px; height: 15px; flex: none; }

  .footer-band {
    position: absolute;
    left: 0; right: 0; top: 348px;
    height: 31px;
    display: flex;
  }
  .footer-band__web {
    flex: 0 0 600px;
    background: var(--green);
    color: var(--white);
    font-family: "Roboto", sans-serif;
    font-size: 16.5px;
    letter-spacing: 0.6px;
    display: flex;
    align-items: center;
    justify-content: center;
    padding-right: 250px;
    box-sizing: border-box;
  }
  .footer-band__accent { flex: 1; background: var(--gold); }
</style>
</head>
<body>
<main class="canvas">

  <section class="card card--front" aria-label="Card front">
    <span class="brand-circle" aria-hidden="true"></span>
    <h1 class="wordmark">
      <span class="wordmark__name">veloran</span>
      <span class="wordmark__sub">Cabinets</span>
    </h1>
  </section>

  <section class="card card--back" aria-label="Card back">
    <span class="brand-circle" aria-hidden="true"></span>
    <p class="wordmark">
      <span class="wordmark__name">veloran</span>
      <span class="wordmark__sub">Cabinets</span>
    </p>

    <span class="divider" aria-hidden="true"></span>

    <div class="contact">
      <h2 class="contact__name"><span class="contact__first">Mitchell</span> <span class="contact__last">Tarrowby</span></h2>
      <p class="contact__role">Director Craftsman</p>
      <ul class="contact__list">
        <li class="contact__item">
          <svg class="contact__icon" viewBox="0 0 16 16" aria-hidden="true">
            <rect x="1.5" y="1.5" width="13" height="13" rx="3" fill="none" stroke="var(--gold)" stroke-width="1.5"/>
          </svg>
          @veloran.cabinets
        </li>
        <li class="contact__item">
          <svg class="contact__icon" viewBox="0 0 16 16" aria-hidden="true">
            <rect x="1" y="3" width="14" height="10" fill="none" stroke="var(--gold)" stroke-width="1.5"/>
            <path d="M1 3 L8 9 L15 3" fill="none" stroke="var(--gold)" stroke-width="1.5"/>
          </svg>
          info@veloranjoinery-example.com.au
        </li>
      </ul>
    </div>

    <div class="footer-band">
      <div class="footer-band__web">www.veloranjoinery-example.com.au</div>
      <div class="footer-band__accent" aria-hidden="true"></div>
    </div>
  </section>

</main>
</body>
</html>
```